Set up small scale company website

We need a website set up for our educational consultancy - Vexmore Education. We like the following site and want something similar www.plindarhub.co.uk We can provide the copy and images but need the following:- setting up the overall theme and design - to our requirements on colours and forma- Approximately 4 pages of services offered and with an index pageEtct (yellow and green)And the following pages - as well as a home page:- A contact page linked to our email addresses and registered business address 17 Wexbury Lane, Harwich, Essex, CO14 8PN- About Us page - An index of services page that links to between 4-6 pages outlining services- A News page that links to updates of latest services, events and activities - easily updated by usOn the homepage we'd like links to chirpnet and WorkLoop feeds and links to our other blogs and websites
Target Market(s)
Schools, local authoroties and multi-academy trusts
Logo Text
Vexmore Education
Coding
Coded - Design and coding required
Number of Pages Required
5+ page
Font styles to use
Requirements
Should not have
- No tacky pictures of mortar boards or chalk boards etc.

```html
<!DOCTYPE html>
<html lang="en">
<head>
<meta charset="utf-8">
<title>Vexmore Education</title>
<link href="https://fonts.googleapis.com/css2?family=Montserrat:wght@400;500;600;700&display=swap" rel="stylesheet">
<style>
:root{
  --green:#9fcb2f;
  --green-band:#a6cd33;
  --green-band-2:#acd237;
  --ink:#222;
  --text:#555;
  --muted:#777;
  --light:#f1f1f1;
  --footer:#151515;
  --white:#fff;
  --panel:#a9abad;
}
*{box-sizing:border-box;margin:0;padding:0}
html,body{width:1200px;height:3020px;overflow:hidden}
body{font-family:'Montserrat',sans-serif;color:var(--ink);background:var(--white);position:relative}
a{color:inherit;text-decoration:none}
.btn{display:inline-block;border:2px solid #333;padding:11px 26px;font-size:16px;font-weight:500;color:#333}
.btn-light{border-color:var(--white);color:var(--white)}

/* header */
.site-header{height:90px;display:flex;align-items:center;justify-content:space-between;padding:0 114px}
.brand{display:flex;align-items:center;gap:14px;font-weight:700;font-size:22px;line-height:1.05;color:#222}
.brand-dot{width:46px;height:46px;border-radius:50%;background:var(--green)}
.main-nav{display:flex;gap:36px;font-size:15px;color:#444}

/* hero */
.hero{position:relative;height:560px;background:linear-gradient(90deg,#4b4b4b,#8a7a6c 45%,#5d5a58 75%,#3e3e3e);text-align:center;color:var(--white)}
.hero-photo{position:absolute;inset:0}
.hero-shade{position:absolute;inset:0;background:rgba(0,0,0,.28)}
.hero-copy{position:relative;padding-top:185px}
.hero-copy .eyebrow{font-size:34px;font-weight:500}
.hero-copy h1{font-size:62px;font-weight:600;margin-top:4px}
.hero-copy p{font-size:17px;font-weight:600;line-height:1.5;width:460px;margin:6px auto 0}
.hero-copy .btn{margin-top:32px;border-color:var(--white);color:var(--white);padding:10px 24px}
.dots{display:flex;gap:8px;justify-content:center;margin-top:28px}
.dots span{width:11px;height:11px;border-radius:50%;background:var(--white)}
.dots span.off{background:transparent;border:2px solid var(--white)}

/* about */
.about{text-align:center;padding:110px 0 100px}
.section-title{color:var(--green);font-size:40px;font-weight:600}
.about p{width:850px;margin:34px auto 0;font-size:17px;line-height:32px;color:var(--text)}
.about .btn{margin-top:32px}

/* tabs */
.focus{position:relative;height:448px}
.tab-list{position:absolute;left:110px;top:0;width:238px;border-left:3px solid var(--green);list-style:none}
.tab-list li{height:58px;line-height:50px;padding-left:18px;font-size:18px;color:#333}
.tab-list li.active{background:var(--green);color:var(--white);height:50px;margin-bottom:8px}
.focus-panel{position:absolute;left:415px;top:8px;right:0;height:440px;background:var(--panel);color:var(--white)}
.focus-photo{position:absolute;right:0;top:0;width:400px;height:100%;background:linear-gradient(135deg,#b9b3aa,#6f7480 55%,#c4c1bb)}
.focus-copy{position:absolute;left:40px;top:70px;width:312px}
.focus-copy h2{font-size:30px;font-weight:600}
.focus-copy p{font-size:14px;line-height:27px;text-align:justify;margin-top:20px}
.focus-copy .btn{margin-top:26px;padding:12px 34px}

/* feeds */
.feeds{display:flex;height:442px}
.feed{flex:1;background:var(--green-band);position:relative}
.feed.alt{background:var(--green-band-2)}
.feed-title{position:absolute;top:74px;left:140px;display:flex;align-items:center;gap:18px;color:var(--white);font-size:31px;font-weight:600}
.feed.alt .feed-title{left:130px}
.feed-mark{width:26px;height:26px;border-radius:50%;background:var(--white)}
.post-card{position:absolute;left:136px;top:158px;width:360px;height:192px;background:var(--white);border-radius:4px;padding:20px 22px}
.feed.alt .post-card{left:128px}
.post-head{display:flex;gap:12px}
.avatar{width:44px;height:44px;border-radius:50%;background:#c9b49d;flex:none}
.post-name{color:var(--green);font-size:19px;font-weight:500}
.post-handle{font-size:12px;font-weight:600;color:#555;margin-top:4px}
.post-body{margin-left:56px;font-size:13px;line-height:22px;color:#777;margin-top:6px}
.post-foot{margin:16px 0 0 56px;display:flex;align-items:center;gap:22px;font-size:14px;color:#444}
.post-foot .date{margin-left:auto;margin-right:16px}
.slider-bars{position:absolute;top:378px;left:240px;display:flex;gap:8px}
.feed.alt .slider-bars{left:232px}
.slider-bars span{width:34px;height:3px;background:rgba(255,255,255,.7)}
.slider-bars span.on{background:var(--white);height:5px;margin-top:-1px}

/* blog */
.blog{background:var(--light);height:612px;padding-top:58px}
.blog .section-title{text-align:center}
.blog-grid{display:flex;gap:26px;margin:32px 0 0 112px}
.blog-card{width:308px}
.blog-photo{height:168px}
.blog-meta{display:flex;gap:14px;margin-top:20px}
.date-box{width:44px;height:42px;border:1px solid #bbb;background:var(--white);text-align:center;font-size:12px;line-height:15px;padding-top:5px;color:#444;flex:none}
.blog-meta h3{font-size:18px;font-weight:500;line-height:24px;color:#222}
.blog-card p{font-size:14px;line-height:24px;color:#666;margin-top:14px}
.blog-card .btn{margin-top:26px;padding:9px 24px;font-size:15px;border-color:#555}

/* footer */
.site-footer{background:var(--footer);height:380px;color:var(--white);position:relative}
.footer-brand{position:absolute;left:142px;top:92px;display:flex;align-items:center;gap:14px;font-size:22px;font-weight:700;line-height:1.05}
.footer-col{position:absolute;top:76px}
.footer-col h4{font-size:20px;font-weight:500;margin-bottom:20px}
.newsletter{left:433px;width:200px}
.newsletter p{font-size:13px;line-height:20px}
.newsletter label{display:block;font-size:10px;margin-top:30px;padding-bottom:8px;border-bottom:1px solid #555;width:168px}
.signup{display:inline-block;margin-top:28px;background:var(--green);border-radius:20px;padding:9px 24px;font-size:14px;font-weight:600;color:#111}
.links{left:685px}
.links ul{list-style:none;font-size:14px;line-height:26px}
.contact{left:875px;width:250px}
.contact-row{display:flex;gap:18px;font-size:14px;line-height:22px;margin-bottom:22px;align-items:flex-start}
.contact-row svg{flex:none}
.footer-bottom{position:absolute;left:114px;right:114px;top:300px;border-top:1px solid #2c2c2c;padding-top:28px;display:flex;justify-content:space-between;font-size:12px}
.socials{display:flex;gap:16px;margin-top:-6px;align-items:center;font-size:11px}
.socials span.on{background:var(--green);border-radius:12px;padding:4px 10px;color:#111}
</style>
</head>
<body>

<header class="site-header">
  <a class="brand" href="#"><span class="brand-dot"></span><span>Vexmore<br>Education</span></a>
  <nav class="main-nav"><a href="#">Home</a><a href="#">About Us</a><a href="#">Services</a><a href="#">News</a><a href="#">Contact Us</a></nav>
</header>

<section class="hero">
  <div class="hero-photo" role="img" aria-label="Group of smiling professionals and students standing together, one holding colourful folders"></div>
  <div class="hero-shade"></div>
  <div class="hero-copy">
    <div class="eyebrow">Welcome To</div>
    <h1>Vexmore Education</h1>
    <p>Lorem ipsum dolor sit amet, consectetur adipiscing elit, sed do eiusmod tempor</p>
    <a class="btn" href="#">Read More</a>
    <div class="dots"><span class="off"></span><span></span><span></span></div>
  </div>
</section>

<section class="about">
  <h2 class="section-title">About Us</h2>
  <p>Lorem ipsum dolor sit amet, consectetur adipiscing elit, sed do eiusmod tempor incididunt ut labore et dolore magna aliqua. Ut enim ad minim veniam, quis nostrud exercitation ullamco laboris nisi ut aliquip ex ea commodo consequat. Duis aute irure dolor in reprehenderit in voluptate velit esse cillum dolore eu fugiat nulla pariatur.</p>
  <a class="btn" href="#">Read More</a>
</section>

<section class="focus">
  <ul class="tab-list">
    <li class="active">Learning</li><li>Education</li><li>Programming</li><li>Self -Awareness</li><li>Community</li><li>More</li>
  </ul>
  <div class="focus-panel">
    <div class="focus-photo" role="img" aria-label="Top-down view of a team working with laptops around a round table"></div>
    <div class="focus-copy">
      <h2>Personnel</h2>
      <p>Lorem ipsum dolor sit amet, consectetur adipiscing elit, sed do eiusmod tempor incididunt ut labore et dolore magna aliqua. Ut enim ad minim veniam, quis nostrud exercitation ullamco laboris nisi ut aliquip ex ea commodo consequat.</p>
      <a class="btn btn-light" href="#">Read More</a>
    </div>
  </div>
</section>

<section class="feeds">
  <div class="feed">
    <div class="feed-title"><span class="feed-mark"></span>chirpnet</div>
    <article class="post-card">
      <div class="post-head"><div class="avatar" role="img" aria-label="Profile photo"></div><div><div class="post-name">Elin Hart</div><div class="post-handle">@Elin Hart</div></div></div>
      <p class="post-body">Sed ut perspiciatis unde omnis iste natus error sit voluptatem accusantium doloremque</p>
      <div class="post-foot">
        <svg width="16" height="14" viewBox="0 0 16 14"><path d="M8 13S1 8.5 1 4.3A3.3 3.3 0 0 1 8 3a3.3 3.3 0 0 1 7 1.3C15 8.5 8 13 8 13z" fill="none" stroke="#444" stroke-width="1.4"/></svg>
        <svg width="16" height="14" viewBox="0 0 16 14"><path d="M9 1H2v12h7M6 7h9M12 4l3 3-3 3" fill="none" stroke="#444" stroke-width="1.4"/></svg>
        <span class="date">Jan 18, 2019</span>
      </div>
    </article>
    <div class="slider-bars"><span></span><span class="on"></span><span></span></div>
  </div>
  <div class="feed alt">
    <div class="feed-title"><span class="feed-mark"></span>WorkLoop</div>
    <article class="post-card">
      <div class="post-head"><div class="avatar" role="img" aria-label="Profile photo"></div><div><div class="post-name">Elin Hart</div><div class="post-handle">@Elin Hart</div></div></div>
      <p class="post-body">Sed ut perspiciatis unde omnis iste natus error sit voluptatem accusantium doloremque</p>
      <div class="post-foot">
        <svg width="16" height="14" viewBox="0 0 16 14"><path d="M8 13S1 8.5 1 4.3A3.3 3.3 0 0 1 8 3a3.3 3.3 0 0 1 7 1.3C15 8.5 8 13 8 13z" fill="none" stroke="#444" stroke-width="1.4"/></svg>
        <svg width="16" height="14" viewBox="0 0 16 14"><path d="M9 1H2v12h7M6 7h9M12 4l3 3-3 3" fill="none" stroke="#444" stroke-width="1.4"/></svg>
        <span class="date">Jan 18, 2019</span>
      </div>
    </article>
    <div class="slider-bars"><span></span><span class="on"></span><span></span></div>
  </div>
</section>

<section class="blog">
  <h2 class="section-title">Our Blog</h2>
  <div class="blog-grid">
    <article class="blog-card">
      <div class="blog-photo" role="img" aria-label="Students gathered around a laptop in a bright classroom" style="background:linear-gradient(135deg,#e7ddd3,#9c8476 55%,#d9d2cb)"></div>
      <div class="blog-meta"><div class="date-box">29<br>Jan</div><h3>At vero eos et accusamus et iusto odio</h3></div>
      <p>Lorem ipsum dolor sit amet, consectetur adipiscing elit, sed do eiusmod tempor incididunt ut labore et dolore.</p>
      <a class="btn" href="#">Read More</a>
    </article>
    <article class="blog-card">
      <div class="blog-photo" role="img" aria-label="Group of students reading together outdoors in a sunny park" style="background:linear-gradient(135deg,#c9d68a,#7d9a4c 50%,#d8b680)"></div>
      <div class="blog-meta"><div class="date-box">29<br>Jan</div><h3>At vero eos et accusamus et iusto odio</h3></div>
      <p>Lorem ipsum dolor sit amet, consectetur adipiscing elit, sed do eiusmod tempor incididunt ut labore et dolore.</p>
      <a class="btn" href="#">Read More</a>
    </article>
    <article class="blog-card">
      <div class="blog-photo" role="img" aria-label="Colleagues in discussion at a whiteboard in an office" style="background:linear-gradient(135deg,#e6e2dc,#a49a90 55%,#d5cec6)"></div>
      <div class="blog-meta"><div class="date-box">29<br>Jan</div><h3>At vero eos et accusamus et iusto odio</h3></div>
      <p>Lorem ipsum dolor sit amet, consectetur adipiscing elit, sed do eiusmod tempor incididunt ut labore et dolore.</p>
      <a class="btn" href="#">Read More</a>
    </article>
  </div>
</section>

<footer class="site-footer">
  <div class="footer-brand"><span class="brand-dot"></span><span>Vexmore<br>Education</span></div>
  <div class="footer-col newsletter">
    <h4>Newsletter</h4>
    <p>Subscribe to us to get and receive the latest news, sales and updates.</p>
    <label>Email Address</label>
    <a class="signup" href="#">Sign Up</a>
  </div>
  <div class="footer-col links">
    <h4>Links</h4>
    <ul><li>Home</li><li>About Us</li><li>Services</li><li>News</li><li>Contact Us</li></ul>
  </div>
  <div class="footer-col contact">
    <h4>Contact Us</h4>
    <div class="contact-row"><svg width="18" height="24" viewBox="0 0 18 24"><path d="M9 23s7-8 7-13A7 7 0 0 0 2 10c0 5 7 13 7 13z" fill="none" stroke="#9fcb2f" stroke-width="1.6"/><circle cx="9" cy="10" r="2.5" fill="none" stroke="#9fcb2f" stroke-width="1.6"/></svg><span>17 Wexbury Lane, Harwich,<br>Essex, CO14 8PN</span></div>
    <div class="contact-row"><svg width="22" height="22" viewBox="0 0 22 22"><path d="M5 2l4 4-2 3c1 3 3 5 6 6l3-2 4 4-3 3C9 20 2 13 2 5z" fill="none" stroke="#9fcb2f" stroke-width="1.6"/></svg><span>(987) 555 0142</span></div>
    <div class="contact-row"><svg width="24" height="18" viewBox="0 0 24 18"><rect x="1" y="1" width="22" height="16" fill="none" stroke="#9fcb2f" stroke-width="1.6"/><path d="M1 1l11 9 11-9" fill="none" stroke="#9fcb2f" stroke-width="1.6"/></svg><span>info@vexmoreeducation.com</span></div>
  </div>
  <div class="footer-bottom">
    <span>Copyright © 2019 All Rights are Reserved.</span>
    <div class="socials"><span>chirpnet</span><span class="on">Folkspace</span><span>WorkLoop</span><span>Orbitplus</span></div>
  </div>
</footer>

</body>
</html>
```